Handmade candle business in melbourne requiring assistance with designing classy labels

My business name is Wick and Willow.
I specialise in making handmade candles, i'm based in Melbourne.
My moto is "Lovingly hand poured and crafted in Melbourne...with care"
wickwillow@lanterbox.com
0427 816 093

I need some assistance with designing my labels for my glass candles
I really like earthy colours and nothing too bright, but I want it to look classy and elegant and something that stands out from other homemade candle businesses.
I have attached a sample of a design that appeals to me but open to suggestions.

```html
<!DOCTYPE html>
<html lang="en">
<head>
<meta charset="utf-8">
<title>Wick and Willow – Candle Label</title>
<link rel="stylesheet" href="https://fonts.googleapis.com/css2?family=Pinyon+Script&family=Playfair+Display:ital,wght@1,700&family=Nunito:wght@500&display=swap">
<style>
  :root {
    --paper: #ffffff;
    --petal-light: #efe1d3;
    --petal-mid: #e2c9b0;
    --band-dark: #7a4a24;
    --band-mid: #946539;
    --band-edge: #d7b894;
    --center-light: #ead3ba;
    --center-mid: #dcb994;
    --ink-dark: #3e1c06;
    --ink-cream: #fbf0e2;
  }
  html, body {
    margin: 0;
    padding: 0;
    width: 1200px;
    height: 1000px;
    overflow: hidden;
    background: var(--paper);
  }
  .label {
    position: relative;
    width: 1200px;
    height: 1000px;
  }
  .label__art {
    position: absolute;
    inset: 0;
  }
  .label__text {
    position: absolute;
    left: 0;
    width: 1200px;
    text-align: center;
    margin: 0;
    white-space: nowrap;
  }
  .label__name {
    top: 425px;
    font-family: "Pinyon Script", cursive;
    font-size: 124px;
    line-height: 1;
    font-weight: 400;
    color: var(--ink-dark);
  }
  .label__motto {
    top: 588px;
    font-family: "Playfair Display", serif;
    font-style: italic;
    font-weight: 700;
    font-size: 33px;
    line-height: 1;
    color: var(--ink-cream);
    text-shadow: 2px 3px 3px rgba(62, 28, 6, 0.9);
  }
  .label__motto-end {
    top: 655px;
  }
  .label__email {
    top: 708px;
    font-family: "Nunito", sans-serif;
    font-weight: 500;
    font-size: 23px;
    line-height: 1;
    color: var(--ink-dark);
    text-shadow: 0 0 2px var(--ink-cream);
  }
</style>
</head>
<body>
  <main class="label">
    <svg class="label__art" width="1200" height="1000" viewBox="0 0 1200 1000">
      <defs>
        <radialGradient id="petal-wash" cx="50%" cy="50%" r="50%">
          <stop offset="0%" stop-color="var(--petal-mid)"/>
          <stop offset="100%" stop-color="var(--petal-light)"/>
        </radialGradient>
        <linearGradient id="band-fill" x1="0" y1="0" x2="1" y2="1">
          <stop offset="0%" stop-color="var(--band-dark)"/>
          <stop offset="50%" stop-color="var(--band-mid)"/>
          <stop offset="100%" stop-color="var(--band-dark)"/>
        </linearGradient>
        <radialGradient id="center-fill" cx="50%" cy="50%" r="50%">
          <stop offset="0%" stop-color="var(--center-light)"/>
          <stop offset="100%" stop-color="var(--center-mid)"/>
        </radialGradient>
      </defs>
      <ellipse class="label__petals" role="img" aria-label="Soft overlapping flower-petal rosette in pale tan tones behind the label"
               cx="600" cy="522" rx="588" ry="458" fill="url(#petal-wash)"/>
      <ellipse class="label__band" cx="600" cy="526" rx="471" ry="279"
               fill="url(#band-fill)" stroke="var(--band-edge)" stroke-width="3"/>
      <ellipse class="label__center" cx="600" cy="528" rx="400" ry="229"
               fill="url(#center-fill)" stroke="var(--band-edge)" stroke-width="3"/>
    </svg>

    <h1 class="label__text label__name">Wick and Willow</h1>
    <p class="label__text label__motto">Lovingly hand poured and crafted in Melbourne...</p>
    <p class="label__text label__motto label__motto-end">with care</p>
    <p class="label__text label__email">wickwillow@lanterbox.com</p>
  </main>
</body>
</html>
```